Local Roofing/Construction company business needs new biz card design

We need a new business card design, current cards are from the start of this operation and generic at best. We are a local Construction Company (General Contractor) with a majority of our work originating from insurance claims-exterior finish work is the main focus (Roofs-Siding-Gutters etc). Heavily involved with homeowners and the low ball offers they receive from insurance company's after a insurable event takes place. I have attached some of our original logo file(s) below.

```html
<!DOCTYPE html>
<html lang="en">
<head>
<meta charset="utf-8">
<title>Northgate Exteriors – Business Card</title>
<link rel="stylesheet" href="https://fonts.googleapis.com/css2?family=Montserrat:wght@400;500;600&display=swap">
<style>
  :root {
    --backdrop: #1a1b1b;
    --card: #0f1f21;
    --green: #5bb873;
    --ink: #eef0ee;
  }
  * { box-sizing: border-box; margin: 0; padding: 0; }
  html, body {
    width: 1200px;
    height: 1059px;
    overflow: hidden;
    background: var(--backdrop);
    font-family: "Montserrat", sans-serif;
  }
  .canvas { position: relative; width: 1200px; height: 1059px; }

  .card {
    position: absolute;
    background: var(--card);
    border-radius: 18px;
  }
  .card--front { left: 257px; top: 89px; width: 687px; height: 390px; }
  .card--back  { left: 254px; top: 547px; width: 693px; height: 393px; }

  /* Front: company name block */
  .brand {
    position: absolute;
    left: 52px;
    top: 161px;
    width: 262px;
    height: 68px;
    display: flex;
    align-items: center;
    gap: 12px;
    color: var(--green);
    font-weight: 600;
    font-size: 25px;
    letter-spacing: 0.5px;
    line-height: 1.05;
  }
  .brand__mark {
    width: 30px; height: 30px;
    background: var(--green);
    flex: none;
  }

  .divider {
    position: absolute;
    left: 343px;
    top: 124px;
    width: 1.5px;
    height: 142px;
    background: var(--green);
  }

  .person { position: absolute; left: 371px; top: 121px; }
  .person__name {
    color: var(--green);
    font-weight: 600;
    font-size: 24px;
    letter-spacing: 0.8px;
    line-height: 1;
  }
  .person__role {
    margin-top: 5px;
    color: var(--ink);
    font-weight: 400;
    font-size: 17px;
    letter-spacing: 0.3px;
  }

  .contacts { position: absolute; left: 370px; top: 193px; list-style: none; }
  .contacts li {
    display: flex;
    align-items: center;
    height: 26.5px;
    color: var(--ink);
    font-size: 17px;
    letter-spacing: 0.2px;
  }
  .contacts svg { width: 12px; height: 12px; margin-right: 7px; flex: none; }

  .address {
    position: absolute;
    left: 0; right: 0;
    top: 329px;
    text-align: center;
    color: var(--ink);
    font-size: 17px;
    letter-spacing: 0.3px;
  }

  /* Back: centered company name */
  .brand-back {
    position: absolute;
    left: 0; right: 0;
    top: 108px;
    display: flex;
    flex-direction: column;
    align-items: center;
    gap: 14px;
    color: var(--green);
    font-weight: 600;
    font-size: 28px;
    letter-spacing: 0.6px;
    line-height: 1.1;
    text-align: center;
  }
  .brand-back__mark { width: 60px; height: 60px; background: var(--green); }
</style>
</head>
<body>
<main class="canvas">

  <section class="card card--front" aria-label="Business card front">
    <div class="brand">
      <span class="brand__mark"></span>
      <span>NORTHGATE<br>EXTERIORS</span>
    </div>

    <div class="divider"></div>

    <div class="person">
      <h1 class="person__name">MARCUS HALE</h1>
      <p class="person__role">Managing Director</p>
    </div>

    <ul class="contacts">
      <li>
        <svg viewBox="0 0 12 12" aria-hidden="true"><path fill="#5bb873" d="M2.4 0.8 4 0.5l1.1 2.6-1.2.9c.6 1.4 1.6 2.5 3 3.1l.9-1.2 2.6 1.1-.3 1.6c-.2.8-1 1.2-1.8 1C4.8 8.8 2.2 6.2 1.4 2.7 1.2 1.8 1.6 1 2.4.8z"/></svg>
        0491 570 226
      </li>
      <li>
        <svg viewBox="0 0 12 12" aria-hidden="true"><path fill="#5bb873" d="M1 4.5 6 1l5 3.5V11H1z"/><path fill="#0f1f21" d="M2 5l4 3 4-3v.9L6 9 2 5.9z"/></svg>
        info@northgateexteriors.com
      </li>
      <li>
        <svg viewBox="0 0 12 12" aria-hidden="true"><circle cx="6" cy="6" r="5.5" fill="#5bb873"/><path fill="#0f1f21" d="M3 3.5c1 0 1.5.8 2.4.6.5 1-.4 1.6-1.2 2-.3 1-.8 1.5-1.6 1.4L2 5c0-.7.4-1.3 1-1.5zM7.5 6.5c.8-.2 1.6.3 1.8 1.1-.4.9-1 1.6-1.9 2-.4-.8-.3-2-.1-3.1z"/></svg>
        www.northgateexteriors.com
      </li>
    </ul>

    <p class="address">1450 W Harlan Road Ashford County Name 5120</p>
  </section>

  <section class="card card--back" aria-label="Business card back">
    <div class="brand-back">
      <span class="brand-back__mark"></span>
      <span>NORTHGATE<br>EXTERIORS</span>
    </div>
  </section>

</main>
</body>
</html>
```